BRIGHTHOLD PROPERTY MANAGEMENT INC. WEBSITE

Please make the website more family-friendly.

I want a website to help me build my property management business by adding listing properties and creating an online application. Im open to any other ideas.
I want a WordPress designer to code it.

Here is my current website. www.brighthold.biz

IDEA: I like the website design https://www.pelicanclimateservices.com/

Thank you

Tom

Number of Pages Required

5+ page

```html
<!DOCTYPE html>
<html lang="en">
<head>
<meta charset="utf-8">
<title>Brighthold Property Management</title>
<link href="https://fonts.googleapis.com/css2?family=Poppins:wght@400;500;600;700&display=swap" rel="stylesheet">
<style>
:root{
  --red:#a3161a;
  --red-dark:#6b0000;
  --red-box:#9b1214;
  --ink:#222222;
  --text:#444444;
  --pink:#f6e4e5;
  --footer:#1c1c1c;
  --white:#ffffff;
  --line:#dddddd;
}
*{margin:0;padding:0;box-sizing:border-box}
html,body{width:1200px;height:3798px;overflow:hidden}
body{font-family:"Poppins",sans-serif;color:var(--text);background:var(--white);position:relative}
.abs{position:absolute}

/* header */
.site-header{position:absolute;left:0;top:0;width:1200px;height:75px;background:var(--white)}
.brand{position:absolute;left:113px;top:18px;display:flex;align-items:center;gap:8px;color:var(--red);font-weight:600;font-size:17px;letter-spacing:1px}
.brand-mark{width:14px;height:14px;background:var(--red)}
.main-nav{position:absolute;top:26px;left:0;font-size:14px;color:var(--ink)}
.main-nav span{position:absolute;white-space:nowrap}
.main-nav .active{color:var(--red)}
.login-btn{position:absolute;left:1001px;top:15px;width:95px;height:42px;background:var(--red);color:var(--white);font-weight:600;font-size:14px;display:flex;align-items:center;justify-content:center}

/* hero */
.hero{position:absolute;left:0;top:75px;width:1200px;height:567px;background:linear-gradient(180deg,#9a7fb3 0%,#c89aa8 30%,#7c7a86 55%,#4a4d55 80%,#6e6a62 100%)}
.hero h1{position:absolute;top:38px;width:100%;text-align:center;color:var(--white);font-size:40px;font-weight:700}
.hero .offer{position:absolute;top:102px;width:100%;text-align:center;color:var(--white);font-size:18px;font-weight:500}
.search{position:absolute;left:351px;top:146px;width:498px;height:44px;display:flex}
.search .field{flex:1;background:#eef5f7;color:#999;font-size:12px;font-style:italic;padding:0 18px;display:flex;align-items:center}
.search .btn{width:96px;background:var(--red);color:var(--white);font-weight:600;font-size:14px;display:flex;align-items:center;justify-content:center}
.dots{position:absolute;top:525px;left:570px;display:flex;gap:6px;align-items:center}
.dots i{width:8px;height:8px;border:1px solid #ddd;border-radius:50%;display:block}
.dots i.on{width:11px;height:11px;background:var(--red);border-color:var(--red)}

/* intro */
.intro-title{position:absolute;top:720px;width:100%;text-align:center;color:var(--ink);font-size:31px;font-weight:700;line-height:41px}
.copy{position:absolute;font-size:15px;line-height:24.7px;text-align:justify}
.copy p{margin-bottom:24px}
.areas{position:absolute;left:621px;top:933px;width:467px;height:451px;display:flex}
.areas ul{list-style:none;padding:22px 0 0 32px;color:var(--white);font-size:13px;font-weight:500}
.areas ul:first-child{width:197px;background:var(--red-box)}
.areas ul:last-child{flex:1;background:var(--red-dark);padding-left:20px}
.areas li{height:30.8px;display:flex;align-items:center;gap:12px;white-space:nowrap}
.areas li::before{content:"";width:6px;height:6px;border:1.5px solid var(--white);border-radius:50%;flex:none}

/* mortgage */
.rates{position:absolute;left:112px;top:1437px;width:976px;height:329px;border:2px solid var(--red)}
.rates .head,.rates .foot{height:48px;background:var(--red);color:var(--white);font-size:15px;font-weight:500;display:flex;align-items:center;justify-content:center}
.rates .foot{position:absolute;bottom:0;left:0;right:0}
.rates .region{height:49px;background:var(--pink);color:var(--red);font-size:15px;display:flex;align-items:center;justify-content:center}
.rate{position:absolute;font-size:15px;color:var(--ink);white-space:nowrap}
.rate b{font-weight:400;margin-left:12px}
.note{position:absolute;right:24px;top:253px;font-size:15px;color:var(--ink)}

/* listings */
.section-title{position:absolute;top:1822px;width:100%;text-align:center;color:var(--ink);font-size:31px;font-weight:700}
.card{position:absolute;width:472px;text-align:center}
.photo{width:472px;height:368px;position:relative}
.photo::after{content:"";position:absolute;left:17px;top:12px;right:17px;bottom:12px;border:1px solid rgba(255,255,255,.85)}
.card h3{margin-top:34px;color:var(--ink);font-size:29px;font-weight:600;line-height:41px}
.card .addr{margin-top:14px;color:var(--text);font-size:19px;line-height:32px}
.card .price{margin-top:18px;color:var(--ink);font-size:33px;font-weight:600}
.pager{position:absolute;top:3246px;left:451px;display:flex;gap:6px}
.pager span{width:36px;height:36px;border:1px solid var(--line);border-radius:50%;font-size:13px;color:var(--text);display:flex;align-items:center;justify-content:center;background:var(--white)}
.pager span.on{background:var(--red);border-color:var(--red);color:var(--white)}

/* footer */
.site-footer{position:absolute;left:0;top:3361px;width:1200px;height:437px;background:var(--footer);color:var(--white)}
.footer-brand{position:absolute;left:155px;top:140px;width:221px;display:flex;align-items:center;justify-content:center;gap:10px;color:var(--red);font-size:28px;font-weight:600;letter-spacing:1px}
.footer-brand .mark{width:22px;height:22px;background:var(--red)}
.social{position:absolute;left:159px;top:256px;display:flex;gap:8px}
.social i{width:28px;height:28px;background:var(--red);border-radius:3px;display:block}
.fcol{position:absolute;top:92px}
.fcol h4{font-size:16px;font-weight:600;letter-spacing:.5px}
.fcol h4::after{content:"";display:block;width:50px;height:2px;background:var(--red);margin-top:7px}
.fcol ul{list-style:none;margin-top:14px;font-size:12.5px;letter-spacing:.4px}
.fcol li{height:26px;display:flex;align-items:center}
.contact-row{position:absolute;left:826px;display:flex;gap:17px;align-items:flex-start}
.contact-row .ico{width:36px;height:36px;border-radius:50%;background:#3a1212;display:flex;align-items:center;justify-content:center;flex:none}
.contact-row small{display:block;font-size:12px;color:#aaa}
.contact-row p{font-size:13.5px;line-height:19px}
.footer-rule{position:absolute;left:112px;top:359px;width:976px;height:1px;background:var(--red)}
.copyright{position:absolute;top:383px;width:100%;text-align:center;font-size:13px}
.to-top{position:absolute;left:1114px;top:339px;width:40px;height:40px;background:var(--red);border-radius:6px;display:flex;align-items:center;justify-content:center}
</style>
</head>
<body>

<header class="site-header">
  <div class="brand"><span class="brand-mark"></span>BRIGHTHOLD</div>
  <nav class="main-nav">
    <span class="active" style="left:274px">Home</span>
    <span style="left:352px">Listings</span>
    <span style="left:442px">Owners</span>
    <span style="left:532px">Prospect Tenants</span>
    <span style="left:690px">About</span>
    <span style="left:769px">Community</span>
    <span style="left:888px">Mortgage Info</span>
  </nav>
  <div class="login-btn">LOGIN</div>
</header>

<section class="hero" role="img" aria-label="Photo of a modern two-storey house with lit garage doors at dusk">
  <h1>Call Today</h1>
  <p class="offer">&amp; Get 1 Month Property Management Fee Off. $120 Value!!</p>
  <div class="search"><div class="field">enter address, city, zip, neighborhood or #MLS</div><div class="btn">SEARCH</div></div>
  <div class="dots"><i></i><i class="on"></i><i></i><i></i></div>
</section>

<h2 class="intro-title">Property Management Elk Grove, Sacramento<br>&amp; Surrounding Areas</h2>

<div class="copy" style="left:113px;top:833px;width:472px">
  <p>Having the right property manager means having an agent who is committed to helping you and making being a home provider hassle free. I believe clear communication, work ethic, time management, staying focused and knowledge goes a long way in my business.</p>
  <p>Additionally whether you are an experienced investor or a first time home seller or buyer, we can help you in finding the property of your dreams. We truly feel excited and gratified when helping individuals meet their real estate needs. You can count on us to always do what's in your best interest. We pride ourselves on being honest, trustworthy, and knowledgeable in the real estate market. We know how important it is to find your dream home or receive the best offer for your property. Therefore we will make it our responsibility to help you achieve those goals.</p>
  <p>Please feel free to browse our website, you can contact us via e-mailing or better yet contact us personally by calling and setting up an appointment today.</p>
</div>
<div class="copy" style="left:621px;top:833px;width:472px">
  <p>This commitment level has helped us build a remarkable track record of delivering results and maintaining a long lasting business partnership with our clients.</p>
</div>

<div class="areas">
  <ul>
    <li>Sacramento</li><li>Antelope</li><li>Carmichael</li><li>Citrus Heights</li><li>El Dorado County</li><li>El Dorado Hills</li><li>Elverta</li><li>Fair Oaks</li><li>Folsom</li><li>Foothill Farms</li><li>Florin Vicinity</li><li>Land Park / Curtis Park</li><li>Galt</li>
  </ul>
  <ul>
    <li>Elk Grove / Laguna</li><li>Mather</li><li>Natomas</li><li>North Highlands</li><li>Orangevale</li><li>Rancho Cordova / Gold River</li><li>Rancho Cordova / Anatolia &amp; Vicinity</li><li>Rancho Murieta</li><li>Rio Linda</li><li>Rocklin</li><li>Rosemont / Mayhew Vicinity</li><li>Roseville</li><li>West Sacramento</li>
  </ul>
</div>

<section class="rates">
  <div class="head">Mortgage Rates</div>
  <div class="region">National</div>
  <div class="rate" style="left:53px;top:104px">30-Year FHA Rate <b>7.07%</b></div>
  <div class="rate" style="left:53px;top:136px">30-Year Fixed Rate <b>7.31%</b></div>
  <div class="rate" style="left:53px;top:168px">20-Year Fixed Rate <b>7.19%</b></div>
  <div class="rate" style="left:53px;top:200px">15-Year Fixed Rate</div>
  <div class="rate" style="right:24px;top:104px">7.07%</div>
  <div class="rate" style="right:24px;top:136px">30-Year Fixed Rate <b>7.31%</b></div>
  <div class="rate" style="right:24px;top:168px">20-Year Fixed Rate <b>7.19%</b></div>
  <div class="rate" style="right:24px;top:200px">15-Year Fixed Rate <b>6.52%</b></div>
  <div class="note">* Conforming FNMA Loan Amount. Rates may include points.</div>
  <div class="foot">Information updated: 6/14/2024</div>
</section>

<h2 class="section-title">All Listings</h2>

<article class="card" style="left:115px;top:1904px">
  <div class="photo" role="img" aria-label="Listing photo: beige ADU unit with wooden steps under a large tree" style="background:linear-gradient(180deg,#7fb0de 0%,#b9c7a8 45%,#d8c29a 75%,#a98f6c 100%)"></div>
  <h3>Fantastic opportunity<br>2 Bdrm x 1 Bth ADU Unit!!</h3>
  <p class="addr">2140 Elm Crest Ave, Oakland, CA 94621<br>Alameda, US</p>
  <p class="price">$2,000.00</p>
</article>
<article class="card" style="left:616px;top:1904px">
  <div class="photo" role="img" aria-label="Listing photo: single-storey building with lawn and trees under blue sky" style="background:linear-gradient(180deg,#2f7fd6 0%,#8fb8e4 45%,#6d7a58 70%,#5d8a3d 100%)"></div>
  <h3>Fantastic opportunity<br>2 Bdrm x 1 Bth ADU Unit!!</h3>
  <p class="addr">2140 Elm Crest Ave, Oakland, CA 94621<br>Alameda, US</p>
  <p class="price">$2,000.00</p>
</article>
<article class="card" style="left:115px;top:2566px">
  <div class="photo" role="img" aria-label="Listing photo: empty room with white walls and wood-look floor" style="background:linear-gradient(180deg,#ecebe8 0%,#dcd9d3 55%,#8a5a36 75%,#5e3a22 100%)"></div>
  <h3>Fantastic opportunity<br>2 Bdrm x 1 Bth ADU Unit!!</h3>
  <p class="addr">2140 Elm Crest Ave, Oakland, CA 94621<br>Alameda, US</p>
  <p class="price">$2,000.00</p>
</article>
<article class="card" style="left:616px;top:2566px">
  <div class="photo" role="img" aria-label="Listing photo: compact kitchen with white cabinets and refrigerator" style="background:linear-gradient(180deg,#f1f0ed 0%,#d9d8d4 55%,#8c8478 80%,#6a6258 100%)"></div>
  <h3>Fantastic opportunity<br>2 Bdrm x 1 Bth ADU Unit!!</h3>
  <p class="addr">2140 Elm Crest Ave, Oakland, CA 94621<br>Alameda, US</p>
  <p class="price">$2,000.00</p>
</article>

<nav class="pager">
  <span>&lsaquo;</span><span class="on">1</span><span>2</span><span>3</span><span>4</span><span>5</span><span>&rsaquo;</span>
</nav>

<footer class="site-footer">
  <div class="footer-brand"><span class="mark"></span>BRIGHTHOLD</div>
  <div class="social" aria-label="Social links"><i></i><i></i><i></i><i></i><i></i><i></i></div>

  <div class="fcol" style="left:453px">
    <h4>LINKS</h4>
    <ul><li>HOME</li><li>LISTINGS</li><li>OWNERS</li><li>PROSPECT TENANTS</li><li>ABOUT</li><li>COMMUNITY</li><li>MORTGAGE INFO</li></ul>
  </div>
  <div class="fcol" style="left:649px">
    <h4>SUPPORT</h4>
    <ul><li>TEAM</li><li>ABOUT US</li><li>CAREERS</li><li>OUR VALUES</li></ul>
  </div>
  <div class="fcol" style="left:836px">
    <h4>CONTACT US</h4>
  </div>

  <div class="contact-row" style="top:134px">
    <span class="ico"><svg width="14" height="18" viewBox="0 0 14 18"><path d="M7 0a7 7 0 0 0-7 7c0 5 7 11 7 11s7-6 7-11a7 7 0 0 0-7-7zm0 9.5A2.5 2.5 0 1 1 7 4.5a2.5 2.5 0 0 1 0 5z" fill="#a3161a"/></svg></span>
    <div><small>Address</small><p>4870 Harbor Oak Rd. #112<br>Sacramento , CA 95822</p></div>
  </div>
  <div class="contact-row" style="top:211px">
    <span class="ico"><svg width="16" height="16" viewBox="0 0 16 16"><path d="M3 1l3 3-2 2c1 2 3 4 5 5l2-2 3 3-2 3C7 15 1 9 1 3z" fill="#a3161a"/></svg></span>
    <div><small>Call Us</small><p>(916) 555-0148</p></div>
  </div>
  <div class="contact-row" style="top:266px">
    <span class="ico"><svg width="18" height="13" viewBox="0 0 18 13"><rect x="0.5" y="0.5" width="17" height="12" fill="none" stroke="#a3161a"/><path d="M1 1l8 6 8-6" fill="none" stroke="#a3161a"/></svg></span>
    <div><small>Email</small><p>info@brighthold.biz</p></div>
  </div>

  <div class="to-top"><svg width="12" height="8" viewBox="0 0 12 8"><path d="M1 7l5-5 5 5" fill="none" stroke="#fff" stroke-width="1.6"/></svg></div>
  <div class="footer-rule"></div>
  <p class="copyright">©2024. All rights reserved.</p>
</footer>

</body>
</html>
```